Road Construction Company needs business cards

We would like a new business card designed for our business.

We're a road construction company based in Qld, Australia.

Can the business card please have the following information on it.

Name: Warren Halbeck
Position: General Manager
Phone: 0472 915 348
Email: Warren.halbeck@tovrin.com.au
Address: 87 Marrow Ave, Pendlebay, QLD, 4023
Website: www.tovrin.com.au

Visually we'd like the card to be professional and simple.

Attached is our logo.

Our website is www.tovrin.com.au

Target Market(s)

Men aged 25-60

Contact Information for Business Card

As listed in project description

Font styles to use
Serif

Requirements
Must have
• Large logo on back of card

```html
<!DOCTYPE html>
<html lang="en">
<head>
<meta charset="utf-8">
<title>Tovrin Business Card</title>
<link rel="stylesheet" href="https://fonts.googleapis.com/css2?family=Open+Sans:wght@400;600;700;800&display=swap">
<style>
  :root {
    --navy: #1456a6;
    --sky: #45abdc;
    --paper: #ffffff;
    --ink: #111111;
    --backdrop: #222327;
  }
  * { box-sizing: border-box; margin: 0; padding: 0; }
  html, body { width: 1200px; height: 780px; overflow: hidden; }
  body {
    background: var(--backdrop);
    font-family: "Open Sans", Arial, sans-serif;
    display: flex;
    align-items: center;
    justify-content: center;
    gap: 28px;
  }
  .card {
    position: relative;
    width: 560px;
    height: 342px;
    background: var(--paper);
    overflow: hidden;
  }
  .brand {
    position: absolute;
    font-weight: 800;
    color: var(--navy);
    letter-spacing: 0.02em;
    line-height: 1;
  }
  .card-back .brand {
    left: 0; right: 0; top: 50%;
    transform: translateY(-50%);
    text-align: center;
    font-size: 118px;
  }
  .card-front .brand {
    left: 0; right: 0; top: 62px;
    text-align: center;
    font-size: 64px;
  }
  .band-contact {
    position: absolute;
    left: 296px; right: 0;
    top: 146px; height: 94px;
    background: var(--sky);
    padding: 11px 0 0 14px;
    color: var(--paper);
    font-size: 13.5px;
    white-space: nowrap;
  }
  .contact-line {
    display: flex; align-items: center; gap: 8px;
    height: 24px;
  }
  .contact-line svg { width: 13px; height: 13px; flex: none; }
  .band-identity {
    position: absolute;
    left: 0; width: 296px;
    top: 200px; height: 70px;
    background: var(--navy);
    color: var(--paper);
    text-align: right;
    padding: 10px 16px 0 0;
  }
  .person-name {
    font-size: 24px; font-weight: 700; letter-spacing: 0.02em; line-height: 1.15;
    white-space: nowrap;
  }
  .person-role {
    font-size: 16px; font-weight: 600; line-height: 1.3;
  }
  .address {
    position: absolute;
    left: 190px; top: 284px;
    font-size: 17px;
    color: var(--ink);
    white-space: nowrap;
  }
</style>
</head>
<body>
  <section class="card card-back" aria-label="Card back">
    <div class="brand">TOVRIN</div>
  </section>

  <section class="card card-front" aria-label="Card front">
    <div class="brand">TOVRIN</div>

    <div class="band-contact">
      <div class="contact-line">
        <svg viewBox="0 0 24 24" fill="currentColor" aria-hidden="true"><path d="M6.6 10.8a15.1 15.1 0 0 0 6.6 6.6l2.2-2.2a1 1 0 0 1 1-.25 11.4 11.4 0 0 0 3.6.57 1 1 0 0 1 1 1V20a1 1 0 0 1-1 1A17 17 0 0 1 3 4a1 1 0 0 1 1-1h3.5a1 1 0 0 1 1 1c0 1.25.2 2.45.57 3.57a1 1 0 0 1-.25 1z"/></svg>
        <span>0472 915 348</span>
      </div>
      <div class="contact-line">
        <svg viewBox="0 0 24 24" fill="none" stroke="currentColor" stroke-width="2" aria-hidden="true"><circle cx="12" cy="12" r="9"/><path d="M3 12h18M12 3c3 3.2 3 14.8 0 18M12 3c-3 3.2-3 14.8 0 18"/></svg>
        <span>www.tovrin.com.au</span>
      </div>
      <div class="contact-line">
        <svg viewBox="0 0 24 24" fill="none" stroke="currentColor" stroke-width="2" aria-hidden="true"><rect x="3" y="5" width="18" height="14" rx="1"/><path d="M3 6l9 7 9-7"/></svg>
        <span>Warren.halbeck@tovrin.com.au</span>
      </div>
    </div>

    <div class="band-identity">
      <div class="person-name">WARREN HALBECK</div>
      <div class="person-role">General Manager</div>
    </div>

    <div class="address">87 Marrow Ave, Pendlebay, QLD, 4023</div>
  </section>
</body>
</html>
```